Small Business Directory Site Requires a Professional Responsive Web Design

Small Business Directory and Coupon Site - we require a complete website design for a brand new responsive & mobile friendly website. We already have a coder who will professional code our website in Magento.

All PSD pages need to be professionally designed then uploaded into a sharedrive (i.e. like filecrate). Additionally, as I cannot pre-empt everything, please note that we may require a little more assistance once the files have been transferred (for example, in www.brightlane-listings.example if you hover your mouse on the search box you will see a pop up box. We want one of these too and I think that means there may be extra design work here)

We have some draft page sketches have been created (there are some minor changes we want to the sketches provided though); however, we require an excellent designer to add the creative touches to it to make it look professionally created. All artwork/font must be legal.

-------------------------
We like the look of the www.brightlane-listings.example and www. marlowfolio.example

For the headers, please consider a font similar to RNS camellia. We likes this style, but it is too thin for the headers...so we need a variation like this one. For the copy/general text font, something basic that marries well with the headers.

---------------------

Please be sure to also read the brief we wrote for the coder as this will help with better understanding our design requirements.

In total I believe we have about 50 pages. This includes all the little pages and most of the pop up boxes (but not the little help key boxes). For example, pages include...

1. Login (this is where customers log in and can edit, manage their profiles. This means that there are backend membership pages)
2. Mini Services (same look and feel as the business coupons)
3. Resource Centre
4. Join (this is where customers learn about the packages available to submit a directory listing, if they ‘buy’ a package (i.e. free, $25 or $150 package) then they can create their own directory listing)
5. Search the directory (customer can view all the categories and also search the directory)
6. Create a directory listing (this is where customers learn about the packages available to submit a directory listing, if they ‘buy’ a package (i.e. free, $25 or $150 package) then they can create their own directory listing)
7. Quote finder (also know as Get a Quote)
8. Coupons (customer go to the business coupon page and can view all current coupons/submit a coupon)
9. Submit a coupon (form)
10.Advertise with us (form)
11. Join the forum
12.Submit an article or video (form)
13. Affiliates (listing of affiliates we currently have)
14. Become an affiliate (form)
15. Case studies (customer can view the case studies we have in the resource centre)
16. Help Guides (customer can view the help guides we have in the resource centre)
17. About Us
18 .Contact Us (form)
19. Terms & Condition
20. Privacy Policy
21. Supporting City Councils
22. Site Map
23. Forgot password / login details
24. Homepage
25. If we hover over a few areas (i.e. search box, location field) it pops up with more information.
etc etc etc. . . there are more pages.

Please see our filecrate link for the draft mock up pages that I have created so far.

https://www.cloudtrunk.example/sh/qk72pmw4rtz8nd/KLMvbTq2fWndxPzs8Yh4ecRQu

We are in a rush! We'd like to get the majority of the artwork completed by the end of the month. Minor fixes/tweaks can occur thereafter.

Target Market(s)

Small Businesses (employees 0 - 50) located throughout Australia

Industry/Entity Type

Business

Font styles to use
Sans Serif

Requirements
Must have
• Professional. Artwork must be legal (cannot be cut and paste or taken off other websites, must be legally purchased and used).Must look contemporary, fresh, modern.

Absolutely must be a responsive site!
Nice to have
• original work, original photos, original art.

like modern, fresh photos that demonstrate innovation, growth, small business, Australian scenery, stability, goals/passion.
Should not have
• cut and paste graphics, illegal graphics, not purchased graphics.

```html
<!DOCTYPE html>
<html lang="en">
<head>
<meta charset="utf-8">
<title>Small Biz Bridge – Australia's Small Business Support Network</title>
<link href="https://fonts.googleapis.com/css2?family=Oswald:wght@400&family=Open+Sans:wght@400;600&display=swap" rel="stylesheet">
<style>
  :root {
    --orange: #f7931e;
    --orange-text: #ee8a12;
    --ink: #555;
    --muted: #7a7a7a;
    --nav: #8a8a8a;
    --band: #f7f7f7;
    --footer: #272220;
    --footer-text: #b6b0aa;
    --footer-head: #d8d2cc;
    --white: #fff;
  }
  * { box-sizing: border-box; margin: 0; padding: 0; }
  html, body { width: 960px; height: 1200px; overflow: hidden; }
  body { font-family: "Open Sans", sans-serif; color: var(--ink); background: var(--white); position: relative; }

  /* header */
  .site-header { position: absolute; left: 0; top: 0; width: 960px; height: 83px; }
  .brand { position: absolute; left: 138px; top: 32px; display: flex; align-items: center; gap: 8px; }
  .brand-mark { width: 18px; height: 18px; background: var(--orange); }
  .brand-name { font-size: 15px; font-weight: 600; color: var(--orange-text); }
  .main-nav { position: absolute; right: 138px; top: 35px; display: flex; gap: 15px; font-size: 12px; color: var(--nav); }

  /* hero */
  .hero { position: absolute; left: 0; top: 83px; width: 960px; height: 370px; overflow: hidden;
    background: linear-gradient(180deg, #0a1550 0%, #12247a 45%, #1d2f8a 62%, #3a3f7a 78%, #1a1a2a 100%); }
  .hero-skyline { position: absolute; left: 0; bottom: 0; width: 960px; height: 120px;
    background: linear-gradient(180deg, rgba(40,40,70,0) 0%, rgba(60,50,80,.7) 40%, #15151f 100%); }
  .hero-title { position: absolute; left: 136px; top: 156px; font-family: "Oswald", sans-serif; font-weight: 400; font-size: 37px; line-height: 1.2; color: var(--white); letter-spacing: -0.8px; }
  .hero-sub { position: absolute; left: 137px; top: 210px; font-family: "Oswald", sans-serif; font-weight: 400; font-size: 27px; line-height: 1.2; color: var(--white); letter-spacing: -0.5px; }
  .search-field { position: absolute; top: 263px; height: 32px; background: var(--white); border-radius: 2px; font-size: 9px; color: var(--muted); padding: 11px 10px; }
  .near-label { position: absolute; left: 292px; top: 270px; font-size: 12px; color: #c9cbe0; }
  .search-btn { position: absolute; left: 482px; top: 263px; width: 78px; height: 32px; background: var(--orange); color: var(--white); font-size: 11px; display: flex; align-items: center; justify-content: center; gap: 8px; border-radius: 2px; }

  .directory-card { position: absolute; left: 613px; top: 95px; width: 210px; height: 199px; background: var(--white); padding: 12px 12px 12px 13px; }
  .directory-card h3 { font-size: 17px; font-weight: 400; color: var(--orange-text); }
  .dots { position: absolute; right: 14px; top: 20px; display: flex; gap: 3px; }
  .dots span { width: 9px; height: 9px; border-radius: 50%; background: #ddd; border: 1px solid #ccc; }
  .dots span.on { background: var(--orange); border-color: var(--orange); }
  .directory-card p { margin-top: 10px; font-size: 9.2px; line-height: 17.2px; color: var(--muted); text-align: justify; }
  .btn { display: inline-flex; align-items: center; justify-content: center; background: var(--orange); color: var(--white); font-size: 11.5px; border-radius: 2px; }
  .directory-card .btn { margin-top: 16px; width: 165px; height: 31px; font-size: 12px; }

  /* community */
  .section-title { position: absolute; left: 0; width: 960px; top: 476px; text-align: center; font-size: 20px; font-weight: 600; color: var(--orange-text); }
  .feature { position: absolute; top: 526px; width: 214px; }
  .feature h4 { font-size: 12.5px; font-weight: 400; color: #6a6a6a; }
  .feature-media { margin-top: 12px; width: 214px; height: 120px; }
  .feature p { margin-top: 18px; font-size: 9.6px; line-height: 17.2px; color: var(--muted); text-align: justify; }
  .feature .btn { margin-top: 17px; width: 124px; height: 32px; }
  .partner-tile { background: #f4f5f7; border: 1px solid #e6e6e6; display: flex; align-items: center; justify-content: center; font-size: 17px; font-weight: 600; color: #1a4f9c; }

  /* partner band */
  .partner-band { position: absolute; left: 0; top: 864px; width: 960px; height: 98px; background: var(--band); border-top: 1px solid #ececec; }
  .partner-name { position: absolute; top: 34px; font-size: 26px; font-weight: 600; }

  /* footer */
  .site-footer { position: absolute; left: 0; top: 962px; width: 960px; height: 238px; background: var(--footer); }
  .footer-col { position: absolute; top: 21px; }
  .footer-col h5 { font-size: 13px; font-weight: 400; color: var(--footer-head); margin-bottom: 10px; }
  .footer-col ul { padding: 0; }
  .footer-col li { list-style: none; font-size: 9.2px; line-height: 16.4px; color: var(--footer-text); }
  .social { display: flex; gap: 2px; }
  .social span { width: 25px; height: 25px; border-radius: 50%; border: 1px solid #555; }
  .footer-rule { position: absolute; left: 138px; top: 184px; width: 685px; height: 1px; background: #3a3432; }
  .copyright { position: absolute; left: 0; width: 960px; top: 203px; text-align: center; font-size: 10px; color: var(--footer-text); }
  .copyright span { margin: 0 6px; }
</style>
</head>
<body>

<header class="site-header">
  <div class="brand"><span class="brand-mark"></span><span class="brand-name">Small Biz Bridge</span></div>
  <nav class="main-nav">
    <span>Login</span><span>Join</span><span>Coupons</span><span>Mini Services</span><span>Get a Quote</span><span>Advertise</span><span>Resource Center</span>
  </nav>
</header>

<section class="hero">
  <div class="hero-skyline" role="img" aria-label="Night view of a harbour city skyline and bridge with fireworks"></div>
  <h1 class="hero-title">Let Us Help You Grow.</h1>
  <h2 class="hero-sub">Australia’s Small Business Support Network</h2>
  <div class="search-field" style="left:138px;width:140px">What are you looking for?</div>
  <div class="near-label">Near</div>
  <div class="search-field" style="left:330px;width:140px">Where?</div>
  <div class="search-btn">Search
    <svg width="12" height="12" viewBox="0 0 12 12"><circle cx="5" cy="5" r="3.6" fill="none" stroke="#fff" stroke-width="1.6"/><line x1="7.6" y1="7.6" x2="11" y2="11" stroke="#fff" stroke-width="1.8"/></svg>
  </div>
  <div class="directory-card">
    <h3>Directory</h3>
    <div class="dots"><span class="on"></span><span></span><span></span><span></span></div>
    <p>Our small business directory is maintained to give members choice. We’re open to all businesses, regardless of your location, so long as they service Australian small businesses.</p>
    <span class="btn">Create your free listing!</span>
  </div>
</section>

<h2 class="section-title">Get Real Support from Our Community</h2>

<article class="feature" style="left:138px">
  <h4>How Did You Sort Your Business?</h4>
  <div class="feature-media" role="img" aria-label="Hands working with a tablet and printed charts on a desk" style="background:linear-gradient(135deg,#e9edf2,#cdd6e0 60%,#b9c6d4)"></div>
  <p>Learn from Dana Holloway, a real small business owner. How she started her business and what are the most valuable resources for her right now.</p>
  <span class="btn">Case Study</span>
</article>

<article class="feature" style="left:373px">
  <h4>Why Go with Small Biz Bridge?</h4>
  <div class="feature-media" role="img" aria-label="Video still of a business team meeting in an office" style="background:linear-gradient(135deg,#d7dde3,#aab4bd 55%,#7f8a95);position:relative">
    <svg width="214" height="120" viewBox="0 0 214 120" style="position:absolute;left:0;top:0"><circle cx="107" cy="60" r="21" fill="#fff" fill-opacity=".55"/><polygon points="101,50 101,70 117,60" fill="#fff"/></svg>
  </div>
  <p>What small business owner can’t relate to the ongoing task of attracting new customers? Struggling with cash flow? Or how about not having enough time in the day? It’s obvious that small businesses suffer from a lack of support. And that’s where we come in.</p>
  <span class="btn">whiteboard video</span>
</article>

<article class="feature" style="left:608px">
  <h4>Become an Affiliate</h4>
  <div class="feature-media partner-tile">Harbor Cover Insurance</div>
  <p>If you have a network of small businesses, let us help to create additional value for your members and make money for your network. Talk to us today about how we can help</p>
  <span class="btn">Become an Affiliate</span>
</article>

<section class="partner-band">
  <span class="partner-name" style="left:143px;color:#222">Granfield</span>
  <span class="partner-name" style="left:386px;color:#555">Tallyhub</span>
  <span class="partner-name" style="left:664px;color:#1a3fa8">Norvane</span>
</section>

<footer class="site-footer">
  <div class="footer-col" style="left:138px"><h5>Site Directory</h5><ul>
    <li>Search the Directory</li><li>Create a Directory Listing</li><li>Quote Finder</li><li>Coupons</li><li>Submit a Coupon</li><li>Advertise with us</li></ul></div>
  <div class="footer-col" style="left:275px"><h5>Resources</h5><ul>
    <li>Join the Forum</li><li>Submit an Article or Video</li><li>Affliates</li><li>Become an Affliates</li><li>Case Studies</li><li>Help Guides</li></ul></div>
  <div class="footer-col" style="left:405px"><h5>Popular Categories</h5><ul>
    <li>Join Today</li><li>Join Small Biz Bridge Today</li><li>Join Small Biz Bridge</li></ul></div>
  <div class="footer-col" style="left:549px"><h5>About</h5><ul>
    <li>About us</li><li>Contact us</li><li>Term &amp; Condition</li><li>Privacy Policy</li><li>Supporting City Count</li><li>Site Map</li></ul></div>
  <div class="footer-col" style="left:668px"><h5>Follow us Our Social Media</h5>
    <div class="social"><span style="background:#3b5998"></span><span style="background:#d8453a"></span><span style="background:#2a7ab8"></span><span style="background:#2fa3d8"></span><span style="background:#c4302b"></span></div>
  </div>
  <div class="footer-rule"></div>
  <p class="copyright">© 2014 smallbizbridge.example. All Right Reserved <span></span> Terms &amp; Conditions <span>|</span> Privacy Policy</p>
</footer>

</body>
</html>
```